Quorva - corporate Business Card

We need a good look and innovative business card for a new start up company based in Los Angeles called "Quorva". We are in a payment business, including payment card, app, and ewallet. We are expert in online payment and Card not present (CNP) transaction.
We need an innovative, modern business card.

Our logo font is Aero Matics

Target Market(s)

Startup - Bank - Online Payment - Card Manufacturing

Industry/Entity Type

Startup

Contact Information for Business Card

phone: 555 014 7396 - Address: 4172 Marlowe blvd, Cylver City, CA 90299

Requirements
Must have
• Message: innovative, professional, expert, high tech, trust, online payment expert, security
Nice to have
• no comment
Should not have
• no Comment

```html
<!DOCTYPE html>
<html lang="en">
<head>
<meta charset="utf-8">
<title>Quorva — Business Card</title>
<link rel="stylesheet" href="https://fonts.googleapis.com/css2?family=Exo+2:wght@400;500;600&display=swap">
<style>
  :root {
    --stage: #e6e6e6;
    --paper: #ffffff;
    --ink: #111111;
    --brand-red: #b41f2e;
    --muted-light: #d9d9d9;
    --shadow: rgba(0, 0, 0, 0.18);
  }
  * { box-sizing: border-box; margin: 0; padding: 0; }
  html, body {
    width: 1200px; height: 997px; overflow: hidden;
    background: var(--stage);
    font-family: "Exo 2", Arial, sans-serif;
  }
  .sheet {
    width: 1200px; height: 997px;
    display: flex; flex-direction: column;
    align-items: center; justify-content: center; gap: 64px;
  }
  .card {
    position: relative;
    width: 600px; height: 343px;
    background: var(--paper);
    border-radius: 6px;
    overflow: hidden;
    box-shadow: 0 10px 30px var(--shadow);
  }
  .card-shape { position: absolute; inset: 0; width: 100%; height: 100%; }
  .brand { position: absolute; display: flex; align-items: center; gap: 14px; }
  .brand-dot {
    width: 78px; height: 78px; border-radius: 50%;
    background: var(--brand-red);
  }
  .brand-name {
    font-weight: 500; font-size: 62px; line-height: 1;
    color: var(--brand-red); letter-spacing: 1px;
  }
  /* front */
  .card-front .brand { left: 50%; top: 66px; transform: translateX(-50%); flex-direction: column; gap: 10px; }
  .card-front .brand-dot { width: 92px; height: 92px; }
  .website {
    position: absolute; left: 0; right: 0; bottom: 22px;
    text-align: center; color: var(--muted-light);
    font-size: 15px; letter-spacing: 5px;
  }
  /* back */
  .card-back .brand { left: 96px; top: 76px; }
  .contact {
    position: absolute; left: 170px; bottom: 46px;
    display: flex; align-items: center; gap: 18px;
  }
  .person { text-align: right; }
  .person-name { color: var(--brand-red); font-weight: 600; font-size: 20px; }
  .person-role { color: var(--muted-light); font-size: 13px; margin-top: 2px; }
  .divider { width: 1px; height: 52px; background: var(--muted-light); }
  .details { list-style: none; color: var(--muted-light); font-size: 14px; line-height: 1.35; }
  .details li { display: flex; gap: 10px; align-items: flex-start; }
  .details svg { flex: none; margin-top: 3px; }
</style>
</head>
<body>
<main class="sheet">

  <section class="card card-front" aria-label="Business card front">
    <svg class="card-shape" viewBox="0 0 600 343" preserveAspectRatio="none" aria-hidden="true">
      <path d="M0 225 Q300 330 600 225" fill="none" stroke="var(--brand-red)" stroke-width="4"/>
      <path d="M0 236 Q300 340 600 236 L600 343 L0 343 Z" fill="var(--ink)"/>
    </svg>
    <div class="brand">
      <span class="brand-dot"></span>
      <span class="brand-name">quorva</span>
    </div>
    <p class="website">www.quorva.com</p>
  </section>

  <section class="card card-back" aria-label="Business card back">
    <svg class="card-shape" viewBox="0 0 600 343" preserveAspectRatio="none" aria-hidden="true">
      <path d="M0 238 Q260 165 600 180" fill="none" stroke="var(--brand-red)" stroke-width="4"/>
      <path d="M0 250 Q260 177 600 192 L600 343 L0 343 Z" fill="var(--ink)"/>
    </svg>
    <div class="brand">
      <span class="brand-dot"></span>
      <span class="brand-name">quorva</span>
    </div>
    <div class="contact">
      <div class="person">
        <p class="person-name">Renata Velloso</p>
        <p class="person-role">Gym Trainer</p>
      </div>
      <span class="divider"></span>
      <ul class="details">
        <li>
          <svg width="14" height="12" viewBox="0 0 14 12" aria-hidden="true">
            <path d="M1 4 Q7 -1 13 4 L11 6 L9 4.5 L5 4.5 L3 6 Z M3 7 H11 V11 H3 Z" fill="var(--brand-red)"/>
          </svg>
          <span>555 014 7396</span>
        </li>
        <li>
          <svg width="14" height="11" viewBox="0 0 14 11" aria-hidden="true">
            <rect x="0.5" y="0.5" width="13" height="10" fill="var(--brand-red)"/>
            <path d="M1 1 L7 6 L13 1" fill="none" stroke="var(--ink)" stroke-width="1.2"/>
          </svg>
          <span>4172 Marlowe blvd, Harlow Vale,<br>CA 90299</span>
        </li>
      </ul>
    </div>
  </section>

</main>
</body>
</html>
```